Pull Up Sign for Financial Services Business

Looking to design a pull-up retractable banner for events. A design which I could add a second banner to so something that could flow across more than one banner would be ideal.

I have included my logo and business card so you can get an idea of colours and our branding style.

A disability image will be required on the banner. Dimensions are in image attached.

Target Market(s)

QVAB (Disability) Participants

Industry/Entity Type

Disability/Finance

Other font styles liked:
• Raleway

Requirements
Must have
• Disability Image - match our branding. Text in image uploaded

```html
<!DOCTYPE html>
<html lang="en">
<head>
<meta charset="utf-8">
<title>Clearpath Plan Management – Pull Up Banner</title>
<link href="https://fonts.googleapis.com/css2?family=Raleway:wght@400;600&family=Montserrat:wght@800;900&family=Nunito:wght@600;700&display=swap" rel="stylesheet">
<style>
  :root{
    --page:#ebebeb;
    --white:#ffffff;
    --pink:#c2437c;
    --magenta:#9c2a6b;
    --teal:#13a59d;
    --teal-deep:#0f7f7a;
    --teal-soft:#5bbbb5;
    --teal-dark:#1f5c63;
    --purple:#6d2d8a;
    --ink:#2c3a45;
    --text-teal:#2a6f73;
  }
  *{box-sizing:border-box;margin:0;padding:0}
  html,body{width:1200px;height:1200px;overflow:hidden;background:var(--page)}
  .canvas{position:relative;width:1200px;height:1200px;background:var(--page)}
  .banner{position:absolute;left:350px;top:20px;width:500px;height:1160px;background:var(--white);overflow:hidden;box-shadow:0 4px 18px rgba(0,0,0,.12)}
  .header-panel{position:absolute;left:0;top:40px;width:470px;height:340px;background:linear-gradient(180deg,#b9b9b9 0%,#c9c9c9 50%,#d7d7d7 100%)}
  .header-panel::after{content:"";position:absolute;right:-30px;top:0;width:60px;height:100%;background:linear-gradient(90deg,rgba(255,255,255,0),var(--white))}
  .brand{position:absolute;left:30px;top:58px;display:flex;align-items:center;gap:12px;z-index:3}
  .brand-square{width:70px;height:70px;background:var(--teal-deep)}
  .brand-name{font-family:"Raleway",sans-serif;font-weight:600;font-size:27px;line-height:1.05;color:var(--pink)}
  .headline{position:absolute;left:24px;top:140px;z-index:3}
  .headline-light{display:block;font-family:"Raleway",sans-serif;font-weight:400;font-size:68px;line-height:1;color:var(--pink);letter-spacing:1px}
  .headline-bold{display:block;font-family:"Montserrat",sans-serif;font-weight:900;font-size:74px;line-height:1;color:var(--teal);margin-top:-2px;background:linear-gradient(180deg,#17c4b8 0%,#0f7f7a 100%);-webkit-background-clip:text;background-clip:text;-webkit-text-fill-color:transparent}
  .photo{position:absolute;left:0;top:262px;width:500px;height:434px;z-index:2;background:linear-gradient(180deg,rgba(0,0,0,0) 0%,#d9b48a 18%,#c9a27f 40%,#c8c07a 60%,#7fb9b2 85%,#5bbbb5 100%)}
  .partner-badge{position:absolute;right:16px;top:540px;width:100px;height:100px;border-radius:50%;background:var(--purple);z-index:4}
  .region-band{position:absolute;left:0;top:696px;width:500px;height:44px;background:var(--teal-soft);z-index:4;display:flex;align-items:center;padding-left:24px}
  .region-band span{font-family:"Montserrat",sans-serif;font-weight:800;font-size:19px;color:var(--white)}
  .feature-row{position:absolute;left:0;width:500px;display:grid;grid-template-columns:1fr 1fr 1fr;background:linear-gradient(180deg,#c4c4c4 0%,#e9e9e9 45%,#fafafa 100%)}
  .feature-row.top{top:740px;height:160px}
  .feature-row.bottom{top:900px;height:172px}
  .feature{position:relative;display:flex;flex-direction:column;align-items:center;padding-top:18px;text-align:center}
  .feature + .feature::before{content:"";position:absolute;left:0;top:16px;bottom:12px;border-left:1px dashed #5d6b70}
  .icon-ring{width:70px;height:70px;border-radius:50%;border:1.5px dashed var(--teal-soft);display:flex;align-items:center;justify-content:center;flex:none}
  .icon{width:60px;height:60px;border-radius:50%;background:linear-gradient(135deg,#d02a9a 0%,#8a3e96 45%,#17a39a 100%);display:flex;align-items:center;justify-content:center}
  .icon svg{width:32px;height:32px;fill:none;stroke:var(--white);stroke-width:1.6;stroke-linecap:round;stroke-linejoin:round}
  .feature-label{margin-top:10px;font-family:"Nunito",sans-serif;font-weight:700;font-size:14px;line-height:1.3;color:var(--text-teal)}
  .feature-label.small{font-size:12.5px;margin-top:8px}
  .footer{position:absolute;left:0;bottom:0;width:500px;height:88px;z-index:5}
  .footer svg{position:absolute;inset:0;width:500px;height:88px}
  .phone{position:absolute;left:0;width:500px;top:30px;text-align:center;font-family:"Raleway",sans-serif;font-weight:400;font-size:12px;color:var(--pink)}
  .web{position:absolute;left:92px;top:48px;width:316px;height:18px;border-radius:9px;background:var(--ink);color:var(--white);font-family:"Montserrat",sans-serif;font-weight:800;font-size:10px;letter-spacing:2.6px;display:flex;align-items:center;justify-content:center}
</style>
</head>
<body>
<div class="canvas">
  <div class="banner">
    <div class="header-panel"></div>

    <div class="brand">
      <div class="brand-square"></div>
      <div class="brand-name">Clearpath<br>Plan Management</div>
    </div>

    <h1 class="headline">
      <span class="headline-light">Your plan</span>
      <span class="headline-bold">Your WAY.</span>
    </h1>

    <div class="photo" role="img" aria-label="Photo of two smiling young women, one with Down syndrome, working together at a laptop on a teal desk"></div>
    <div class="partner-badge" role="img" aria-label="Partner badge"></div>

    <div class="region-band"><span>Australia wide plan management</span></div>

    <div class="feature-row top">
      <div class="feature">
        <div class="icon-ring"><div class="icon">
          <svg viewBox="0 0 32 32"><rect x="8" y="5" width="16" height="22" rx="2"/><path d="M12 11h8M12 15h8M12 19h5"/></svg>
        </div></div>
        <p class="feature-label">Invoices<br>processed daily</p>
      </div>
      <div class="feature">
        <div class="icon-ring"><div class="icon">
          <svg viewBox="0 0 32 32"><path d="M9 4h10l5 5v19H9z"/><path d="M19 4v5h5M12 13h9M12 17h5M20 18v7M22 19.5h-3a1.2 1.2 0 0 0 0 2.4h2a1.2 1.2 0 0 1 0 2.4h-3"/></svg>
        </div></div>
        <p class="feature-label small">Providers paid<br>within 3 business<br>days</p>
      </div>
      <div class="feature">
        <div class="icon-ring"><div class="icon">
          <svg viewBox="0 0 32 32"><path d="M6 14h5v12H6zM11 15l5-9c2 0 3 1.5 2.5 3.5L17 13h7a2 2 0 0 1 2 2.3l-1.5 8.5a2 2 0 0 1-2 1.7H11"/></svg>
        </div></div>
        <p class="feature-label">Expense<br>reimbursements</p>
      </div>
    </div>

    <div class="feature-row bottom">
      <div class="feature">
        <div class="icon-ring"><div class="icon">
          <svg viewBox="0 0 32 32"><rect x="5" y="5" width="6" height="6" rx="1"/><rect x="13" y="5" width="6" height="6" rx="1"/><rect x="21" y="5" width="6" height="6" rx="1"/><path d="M15 27v-12a1.5 1.5 0 0 1 3 0v6l4 1v5"/></svg>
        </div></div>
        <p class="feature-label small">Choice and control -<br>use both registered<br>and unregistered<br>providers</p>
      </div>
      <div class="feature">
        <div class="icon-ring"><div class="icon">
          <svg viewBox="0 0 32 32"><path d="M16 17s-6-3.5-6-7.5a3 3 0 0 1 6-1 3 3 0 0 1 6 1c0 4-6 7.5-6 7.5z"/><path d="M5 21h3v6H5zM8 22h12a2 2 0 0 0 0-3h-4"/><path d="M8 26h10l7-5"/></svg>
        </div></div>
        <p class="feature-label">Your own personal<br>dedicated plan<br>manager</p>
      </div>
      <div class="feature">
        <div class="icon-ring"><div class="icon">
          <svg viewBox="0 0 32 32"><rect x="8" y="4" width="14" height="24" rx="2"/><path d="M12 13l2 2 4-4M13 24h4"/></svg>
        </div></div>
        <p class="feature-label">Real time funding<br>access</p>
      </div>
    </div>

    <div class="footer">
      <svg viewBox="0 0 500 88" preserveAspectRatio="none" aria-hidden="true">
        <rect x="0" y="0" width="500" height="88" fill="#2c3a45"/>
        <path d="M0 0 L500 0 L500 88 L150 88 C90 80 40 68 0 52 Z" fill="#9c2a6b"/>
        <path d="M500 0 L500 88 L320 88 C410 70 470 40 500 0 Z" fill="#1f5c63"/>
        <path d="M0 0 H500 C450 60 350 84 250 84 C150 84 50 60 0 0 Z" fill="#ffffff"/>
      </svg>
      <p class="phone">1300 555 218</p>
      <p class="web">WWW.CLEARPATHPLANNING.COM.AU</p>
    </div>
  </div>
</div>
</body>
</html>
```